Public Speaking Book for aspiring, ambitious speakers

I'm looking for a 6x9 book cover (Brivora standard) as well as ebook and audiobook formats.

I'm looking for orange font on a white background as these are my brand colours.

Feel free to use some yellow and gold too if you deem it appropriate.

Title: Climb and Kindle
Subtitle: Find Your Voice. Tell Your Story. Share your Message.
Author: Owen Thistlewood

I would like to have a picture of a female speaker on the front cover.

Alternatively, some kind of image that symbolises public speaking like a microphone, podium etc

Target Market(s)

Aspiring professional speakers

Colors
f78f20

Requirements
Must have
• Correct spelling!
Nice to have
• A logo or picture that fits the theme, but no pressure if you can't think of anything
Should not have
• No men in suits please. I don't want this to have a 1980s corporate look.

```html
<!DOCTYPE html>
<html lang="en">
<head>
<meta charset="utf-8">
<title>Climb and Kindle – Book Cover Spread</title>
<link rel="stylesheet" href="https://fonts.googleapis.com/css2?family=Raleway:ital,wght@0,400;0,500;0,600;0,700;1,400;1,500&display=swap">
<style>
  :root {
    --stage: #2d2d2d;
    --brand-orange: #f78f20;
    --paper: #ffffff;
    --ink: #2b2b2b;
    --art-light: #f3f3f3;
  }
  * { margin: 0; padding: 0; box-sizing: border-box; }
  html, body {
    width: 1200px; height: 1200px; overflow: hidden;
    background: var(--stage);
    font-family: "Raleway", Arial, sans-serif;
  }
  .canvas { position: relative; width: 1200px; height: 1200px; }

  .cover-spread {
    position: absolute; left: 69px; top: 240px;
    width: 1021px; height: 719px;
    display: flex;
  }

  /* Back cover */
  .back-cover {
    width: 479px; height: 100%;
    background: var(--brand-orange);
    position: relative;
    overflow: hidden;
  }
  .back-title {
    position: absolute; top: 0; left: 0; right: 0; height: 140px;
    text-align: center; color: var(--paper);
    line-height: 1; font-weight: 600;
  }
  .back-title span { position: absolute; left: 0; right: 0; display: block; }
  .back-title .title-main { top: 12px; font-size: 64px; letter-spacing: -1px; }
  .back-title .title-join { top: 78px; font-size: 11px; color: var(--ink); letter-spacing: 11px; padding-left: 11px; }
  .back-title .title-end { top: 86px; font-size: 44px; letter-spacing: -0.5px; }
  .back-blurb {
    position: absolute; left: 37px; top: 150px; width: 408px;
    color: var(--paper);
    font-size: 11.6px; line-height: 15px;
    text-align: justify; hyphens: auto;
  }
  .back-blurb p + p { margin-top: 2px; }

  /* Spine */
  .spine {
    width: 61px; height: 100%;
    background: var(--brand-orange);
    border-left: 1px solid rgba(0,0,0,0.12);
    position: relative;
  }
  .spine-title, .spine-author {
    position: absolute; left: 50%;
    writing-mode: vertical-rl;
    transform: translateX(-50%);
    font-weight: 700; white-space: nowrap;
  }
  .spine-title { top: 118px; color: var(--paper); font-size: 23px; letter-spacing: 0.5px; }
  .spine-author { top: 484px; color: var(--ink); font-size: 15px; }

  /* Front cover */
  .front-cover {
    flex: 1; height: 100%;
    background: var(--paper);
    position: relative;
    overflow: hidden;
  }
  .speaker-art {
    position: absolute; left: 21px; top: 32px;
    width: 459px; height: 300px;
    background: linear-gradient(160deg, var(--paper) 0%, var(--art-light) 60%, var(--paper) 100%);
  }
  .tagline {
    position: absolute; right: 237px; top: 60px;
    text-align: right; color: var(--ink);
    font-style: italic; font-size: 19px; line-height: 31px;
    z-index: 1;
  }
  .front-title {
    position: absolute; top: 0; left: 0; right: 0; height: 640px;
    text-align: center; color: var(--brand-orange);
    line-height: 1; font-weight: 600;
  }
  .front-title span { position: absolute; left: 0; right: 0; display: block; }
  .front-title .title-main { top: 340px; font-size: 122px; letter-spacing: -2px; }
  .front-title .title-end { top: 502px; font-size: 122px; letter-spacing: -2px; }
  .front-title .title-join {
    top: 488px; color: var(--ink);
    font-size: 27px; letter-spacing: 38px; padding-left: 38px;
  }
  .front-author {
    position: absolute; top: 662px; left: 0; right: 0;
    text-align: center; color: var(--ink);
    font-size: 23px; font-weight: 600; letter-spacing: 7px;
  }
</style>
</head>
<body>
<div class="canvas">
  <div class="cover-spread">

    <section class="back-cover">
      <h2 class="back-title">
        <span class="title-main">CLIMB</span>
        <span class="title-join">AND</span>
        <span class="title-end">KINDLE</span>
      </h2>
      <div class="back-blurb">
        <p>Every great speaker once stood at the edge of a stage with a dry mouth and a racing heart. Climb and Kindle is a practical guide for anyone who wants to turn that nervous energy into presence, clarity and real connection with an audience. Drawing on years of coaching new voices, Owen Thistlewood shows you how to shape ideas into talks that people remember long after the lights come up.</p>
        <p>You will learn how to find the story only you can tell, build a message with a clear spine, and open every talk in a way that earns attention from the first line. Simple drills make each step easy to practise.</p>
        <p>Inside these pages are tools for calming stage fright, using your breath and body with intent, pacing a room, and handling questions with ease. Each chapter ends with short exercises you can try at home, at work or at your next meetup, so progress feels steady rather than overwhelming. Whether you dream of keynotes, workshops or a single toast that moves a room, this book gives you a path to follow.</p>
        <p>Speaking is not a gift handed to a lucky few. It is a skill, and like any skill it grows with honest practice, kind feedback and the courage to begin before you feel ready.</p>
        <p>Find your voice, tell your story and share your message with the confidence you have always known was there. The stage is waiting, and the people in those seats want to hear what you have to say. Step up, take a breath and let your words light the way for others who are still finding the courage to speak.</p>
      </div>
    </section>

    <section class="spine">
      <span class="spine-title">CLIMB AND KINDLE</span>
      <span class="spine-author">OWEN THISTLEWOOD</span>
    </section>

    <section class="front-cover">
      <div class="speaker-art" role="img" aria-label="Single-line drawing of a woman speaking into a microphone at a podium"></div>
      <p class="tagline">Find Your Voice.<br>Tell Your Story.<br>Share your Message.</p>
      <h1 class="front-title">
        <span class="title-main">CLIMB</span>
        <span class="title-join">AND</span>
        <span class="title-end">KINDLE</span>
      </h1>
      <p class="front-author">OWEN THISTLEWOOD</p>
    </section>

  </div>
</div>
</body>
</html>
```